VENTURE CAPITAL GROUP BUSINESS CARD DESIGN

Venture Capital Group based in SF looking for a bold business card design. No trendy colour explosion, 3D effects etc. Just "simple" optical effects. Works on your brain, keeps your eye focused and sticks to your mind.
Target Market(s)
Technology startups
Industry/Entity Type
Venture Capital
Contact Information for Business Card
DESMOND WHITLAKE
MANAGING PARTNER
187 FENWORTH ST SAN FRANCISCO, CA 94187
415.555.0142 O
415.555.0147 F
415.555.0193 C
desmond@veldtmoorcapital.ventures

```html
<!DOCTYPE html>
<html lang="en">
<head>
<meta charset="utf-8">
<title>Veldtmoor Capital Group – Business Card</title>
<link rel="stylesheet" href="https://fonts.googleapis.com/css2?family=Cinzel:wght@400&family=Open+Sans:ital,wght@0,400;1,400&family=Arimo:wght@400&display=swap">
<style>
  :root {
    --page: #eef0ef;
    --card-white: #ffffff;
    --brand-green: #2f8f1c;
    --pattern-green: #3fbf24;
    --pattern-deep: #2a9a14;
    --band-grey: #98a6ad;
    --type-grey: #8a9499;
    --ink-white: #ffffff;
  }
  * { box-sizing: border-box; margin: 0; padding: 0; }
  html, body { width: 995px; height: 1200px; overflow: hidden; }
  body { background: var(--page); position: relative; font-family: "Arimo", Arial, sans-serif; }

  .card { position: absolute; overflow: hidden; }

  /* Front */
  .card-front { left: 51px; top: 51px; width: 888px; height: 518px; background: var(--card-white); }
  .brand-mark {
    position: absolute; left: 371px; top: 31px; width: 164px; height: 164px; border-radius: 50%;
    background: radial-gradient(circle at 40% 40%, #ffffff 0%, #e6e9ea 70%, #d4d9db 100%);
  }
  .brand-name {
    position: absolute; left: 0; width: 100%; top: 214px; text-align: center;
    font-family: "Cinzel", serif; font-size: 44px; color: var(--brand-green); letter-spacing: 1px;
  }
  .brand-sub {
    position: absolute; left: 0; width: 100%; top: 268px; text-align: center;
    font-family: "Cinzel", serif; font-size: 11px; color: var(--type-grey); letter-spacing: 5px;
  }
  .person-name {
    position: absolute; left: 0; width: 100%; top: 293px; text-align: center;
    font-family: "Open Sans", sans-serif; font-size: 21px; color: var(--brand-green);
  }
  .person-title {
    position: absolute; left: 0; width: 100%; top: 317px; text-align: center;
    font-family: "Open Sans", sans-serif; font-style: italic; font-size: 19px; color: var(--brand-green);
  }
  .divider-band { position: absolute; left: 0; top: 353px; width: 100%; height: 12px; background: var(--band-grey); }
  .contact-band {
    position: absolute; left: 0; top: 367px; width: 100%; height: 151px;
    background: linear-gradient(180deg, var(--pattern-green), var(--pattern-deep));
  }
  .contact-lines {
    position: absolute; left: 50px; top: 14px; color: var(--ink-white);
    font-size: 22px; line-height: 26.5px; text-shadow: 0 0 2px rgba(0,0,0,.6);
    white-space: pre;
  }
  .web-lines {
    position: absolute; right: 42px; top: 73px; text-align: right; color: var(--ink-white);
    font-size: 20px; line-height: 24px; text-shadow: 0 0 2px rgba(0,0,0,.6);
  }

  /* Back */
  .card-back {
    left: 49px; top: 606px; width: 893px; height: 523px;
    background: linear-gradient(180deg, var(--pattern-green), var(--pattern-deep));
  }
  .veil { position: absolute; left: 43px; top: 78px; width: 804px; height: 274px; background: rgba(255,255,255,.14); }
  .back-mark {
    position: absolute; left: 337px; top: 57px; width: 246px; height: 246px; border-radius: 50%;
    background: rgba(255,255,255,.35);
  }
  .back-name {
    position: absolute; left: 0; width: 100%; top: 163px; text-align: center;
    font-family: "Cinzel", serif; font-size: 34px; color: var(--ink-white); letter-spacing: 1px;
  }
  .back-band { position: absolute; left: 0; top: 352px; width: 100%; height: 106px; background: rgba(0,80,0,.22); }
  .back-rule { position: absolute; left: 0; top: 458px; width: 100%; height: 4px; background: rgba(140,255,110,.45); }
  .back-lines {
    position: absolute; left: 0; width: 100%; top: 368px; text-align: center; color: var(--ink-white);
    font-size: 30px; line-height: 39px;
  }
</style>
</head>
<body>
  <section class="card card-front">
    <div class="brand-mark"></div>
    <div class="brand-name">VELDTMOOR</div>
    <div class="brand-sub">CAPITAL GROUP</div>
    <div class="person-name">DESMOND WHITLAKE</div>
    <div class="person-title">Managing Partner</div>
    <div class="divider-band"></div>
    <div class="contact-band" role="img" aria-label="Green background of overlapping concentric circle pattern">
      <div class="contact-lines">187 Fenworth st.  San francisco, CA 94187
415.555.0142 O
415.555.0147 F
415.555.0193 C</div>
      <div class="web-lines">desmond@veldtmoorcapital.ventures<br>www.veldtmoorcapital.com</div>
    </div>
  </section>

  <section class="card card-back" role="img" aria-label="Green background of overlapping concentric circle pattern">
    <div class="veil"></div>
    <div class="back-mark"></div>
    <div class="back-name">VELDTMOOR</div>
    <div class="back-band"></div>
    <div class="back-rule"></div>
    <div class="back-lines">desmond@veldtmoorcapital.ventures<br>www.veldtmoorcapital.com</div>
  </section>
</body>
</html>
```